RW Framewell Inc Business cards

We need business cards using our existing logo but slightly modified. Right now the logo says RW Loadbearing Masonry. We want to keep the RW part of the design, but replace the Structural Concrete portion with "FRAMEWELL". Please see the attached file.
Ideally this would be a blank template so we can add Different Names, titles, and phone numbers later.
On the one side we want only the logo and on the other side the detail. I'm attaching an example for you to see.
Please reach out with any other questions. Our address and other details will be given out once we find a design we like.

Target Market(s)

Construction Industry

```html
<!DOCTYPE html>
<html lang="en">
<head>
<meta charset="UTF-8">
<title>RW Framewell Inc — Business Card</title>
<link href="https://fonts.googleapis.com/css2?family=Roboto:wght@400;500&display=swap" rel="stylesheet">
<style>
  :root {
    --page-bg: #e6e6e4;
    --card-top: #eceae7;
    --divider: #6d6d6d;
    --brand-blue: #2f5f9f;
    --name-blue: #2d5a98;
    --title-grey: #666666;
    --detail-text: #e8eef7;
    --logo-text: #ece6dc;
  }
  * { margin: 0; padding: 0; box-sizing: border-box; }
  html, body {
    width: 1200px;
    height: 1054px;
    overflow: hidden;
    background: var(--page-bg);
    font-family: "Roboto", Arial, sans-serif;
  }
  .business-card {
    position: absolute;
    left: 170px;
    top: 267px;
    width: 860px;
    height: 520px;
    background: var(--card-top);
    box-shadow: 0 10px 30px rgba(0,0,0,0.15);
    overflow: hidden;
  }
  .identity {
    position: absolute;
    left: 47px;
    top: 66px;
  }
  .identity__name {
    font-size: 30px;
    font-weight: 500;
    color: var(--name-blue);
    line-height: 1;
  }
  .identity__title {
    margin-top: 12px;
    font-size: 20px;
    font-weight: 400;
    color: var(--title-grey);
  }
  .divider {
    position: absolute;
    left: 0;
    top: 196px;
    width: 100%;
    height: 11px;
    background: var(--divider);
  }
  .details-band {
    position: absolute;
    left: 0;
    top: 207px;
    width: 100%;
    height: 313px;
    background: var(--brand-blue);
  }
  .address {
    position: absolute;
    left: 47px;
    top: 66px;
    font-size: 21px;
    line-height: 33px;
    color: var(--detail-text);
  }
  .contact-list {
    position: absolute;
    left: 47px;
    top: 148px;
    list-style: none;
    color: var(--detail-text);
    font-size: 21px;
  }
  .contact-list__item {
    display: flex;
    align-items: center;
    height: 32.5px;
  }
  .contact-list__icon {
    width: 20px;
    height: 20px;
    margin-right: 24px;
    fill: var(--detail-text);
  }
  .wordmark {
    position: absolute;
    left: 470px;
    top: 52px;
    width: 334px;
    text-align: center;
    color: var(--logo-text);
    font-weight: 500;
  }
  .wordmark__initials {
    font-size: 118px;
    line-height: 1;
    letter-spacing: 4px;
  }
  .wordmark__name {
    margin-top: 8px;
    font-size: 33px;
    letter-spacing: 5px;
  }
</style>
</head>
<body>
  <article class="business-card">
    <header class="identity">
      <h1 class="identity__name">Mark RW Ellison</h1>
      <p class="identity__title">Managing Director</p>
    </header>

    <div class="divider"></div>

    <section class="details-band">
      <p class="address">58 Harlow Yard Rd., Brookmere,<br>California, US 940217</p>

      <ul class="contact-list">
        <li class="contact-list__item">
          <svg class="contact-list__icon" viewBox="0 0 20 20" aria-hidden="true">
            <path d="M2 7 Q10 1 18 7 L16 9 L13 8 L13 6 Q10 5 7 6 L7 8 L4 9 Z"/>
            <path d="M5 10 L15 10 L17 17 L3 17 Z"/>
          </svg>
          <span>555-204-3187</span>
        </li>
        <li class="contact-list__item">
          <svg class="contact-list__icon" viewBox="0 0 20 20" aria-hidden="true">
            <path d="M2 4 H18 V16 H2 Z M3.5 5.5 L10 11 L16.5 5.5 V14.5 H3.5 Z" fill-rule="evenodd"/>
          </svg>
          <span>mark@framewellbuild.com</span>
        </li>
        <li class="contact-list__item">
          <svg class="contact-list__icon" viewBox="0 0 20 20" aria-hidden="true">
            <circle cx="10" cy="10" r="7.5" fill="none" stroke="currentColor" stroke-width="1.6" style="stroke:var(--detail-text)"/>
            <path d="M2.5 10 H17.5 M10 2.5 V17.5 M10 2.5 Q5 10 10 17.5 M10 2.5 Q15 10 10 17.5" fill="none" style="stroke:var(--detail-text)" stroke-width="1.4"/>
          </svg>
          <span>www.framewellbuild.com</span>
        </li>
      </ul>

      <div class="wordmark">
        <div class="wordmark__initials">RW</div>
        <div class="wordmark__name">FRAMEWELL</div>
      </div>
    </section>
  </article>
</body>
</html>
```